Quillmarsh Property Solutions need a business card design

Hello guys. We would need a business card design asap please.
We are a start up property investment business based in London UK specialised in buying, selling, managing and letting properties and helping distressed property owners.
The name of our Business is Quillmarsh, the logo symbolises the four fundamental elements of the world (earth, air, fire and water) and so it stands for strength, stability, longevity.
We would like the business card to communicate professionalism and reliability. Many many thanks indeed for your work.

Details:

1.) Rosalind Updike
Property Investor
Mobile: +44(0)7700123456
Email: rosalind.quillmarsh@mailbox-example.com

2.) Dominic Updike
Property Investor
Mobile: +44(0)7700987654
Email: dominic.quillmarsh@mailbox-example.com

```html
<!DOCTYPE html>
<html lang="en">
<head>
<meta charset="utf-8">
<title>Quillmarsh Property Solutions – Business Card</title>
<link rel="stylesheet" href="https://fonts.googleapis.com/css2?family=Open+Sans:wght@400;600;700;800&display=swap">
<style>
  :root {
    --canvas-bg: #e9e7e3;
    --card-white: #ffffff;
    --brand-green: #0b5a2a;
    --brand-blue: #2f56a8;
    --ink-dark: #1c1c1c;
    --ink-light: #ffffff;
    --card-shadow: 0 14px 30px rgba(0, 0, 0, 0.18);
  }
  * { box-sizing: border-box; margin: 0; padding: 0; }
  html, body {
    width: 1200px;
    height: 720px;
    overflow: hidden;
    background: var(--canvas-bg);
    font-family: "Open Sans", Arial, sans-serif;
  }
  .canvas {
    width: 1200px;
    height: 720px;
    display: flex;
    align-items: center;
    justify-content: center;
    gap: 50px;
  }
  .card {
    position: relative;
    width: 540px;
    height: 310px;
    box-shadow: var(--card-shadow);
    overflow: hidden;
  }

  /* Front */
  .card--front { background: var(--card-white); }
  .front__brand {
    position: absolute;
    top: 0; left: 0; right: 0;
    height: 148px;
    display: flex;
    flex-direction: column;
    align-items: center;
    justify-content: center;
    padding-top: 8px;
  }
  .brand-lockup {
    display: flex;
    align-items: center;
    gap: 12px;
  }
  .brand-lockup__square {
    width: 22px;
    height: 22px;
    background: var(--brand-green);
  }
  .brand-lockup__name {
    font-weight: 800;
    font-size: 30px;
    letter-spacing: 1px;
    color: var(--ink-dark);
    text-transform: uppercase;
  }
  .brand-tagline {
    margin-top: 2px;
    font-weight: 700;
    font-size: 10px;
    letter-spacing: 1.2px;
    color: var(--ink-dark);
    text-transform: uppercase;
  }
  .front__name-band {
    position: absolute;
    top: 148px; left: 0; right: 0;
    height: 32px;
    background: var(--brand-blue);
    display: flex;
    align-items: center;
    justify-content: center;
    color: var(--ink-light);
    font-size: 17px;
    border-bottom: 3px solid var(--card-white);
  }
  .front__name-band .person-name {
    font-weight: 700;
    text-transform: uppercase;
    letter-spacing: 0.3px;
  }
  .front__name-band .person-role { font-weight: 400; }
  .front__contact {
    position: absolute;
    top: 180px; left: 0; right: 0; bottom: 0;
    background: var(--brand-green);
  }
  .contact-list {
    list-style: none;
    padding-top: 12px;
    display: flex;
    flex-direction: column;
    align-items: center;
    gap: 5px;
    color: var(--ink-light);
    font-size: 13.5px;
  }
  .contact-list li {
    display: flex;
    align-items: center;
    gap: 7px;
  }
  .contact-list svg { width: 13px; height: 13px; fill: var(--ink-light); }
  .front__accent-stripe {
    position: absolute;
    left: 0; right: 0;
    top: 268px;
    height: 12px;
    background: var(--brand-blue);
  }

  /* Back */
  .card--back {
    background: var(--brand-green);
    display: flex;
    align-items: center;
    justify-content: center;
  }
  .card--back .brand-lockup__square { background: var(--ink-light); width: 30px; height: 30px; }
  .card--back .brand-lockup__name { color: var(--ink-light); font-size: 40px; }
</style>
</head>
<body>
<main class="canvas">

  <section class="card card--front" aria-label="Business card front">
    <header class="front__brand">
      <div class="brand-lockup">
        <span class="brand-lockup__square" aria-hidden="true"></span>
        <span class="brand-lockup__name">Quillmarsh</span>
      </div>
      <p class="brand-tagline">Property Solutions</p>
    </header>

    <div class="front__name-band">
      <span class="person-name">Dominic Updike</span><span class="person-role">, Property Investor</span>
    </div>

    <div class="front__contact">
      <ul class="contact-list">
        <li>
          <svg viewBox="0 0 16 16" aria-hidden="true"><path d="M5 1h6a1 1 0 0 1 1 1v12a1 1 0 0 1-1 1H5a1 1 0 0 1-1-1V2a1 1 0 0 1 1-1zm0 2v9h6V3H5zm3 10a.8.8 0 1 0 0 .01z"/></svg>
          <span>+44(0)7700987654</span>
        </li>
        <li>
          <svg viewBox="0 0 16 16" aria-hidden="true"><path d="M1 4h14v9H1V4zm1.5 1 5.5 4 5.5-4h-11z"/></svg>
          <span>dominic.quillmarsh@mailbox-example.com</span>
        </li>
      </ul>
    </div>
    <div class="front__accent-stripe" aria-hidden="true"></div>
  </section>

  <section class="card card--back" aria-label="Business card back">
    <div class="brand-lockup">
      <span class="brand-lockup__square" aria-hidden="true"></span>
      <span class="brand-lockup__name">Quillmarsh</span>
    </div>
  </section>

</main>
</body>
</html>
```